Lendquay wedsite and logo refresh

We are looking for someone to refresh the look and feel of Lendquay.co.nz we are moving it towards a more traditional brokerage.

Target Market(s)

30 to 55 year old professionals

Coding

Coded - Design and coding required

Number of Pages Required

3 page

Requirements
Nice to have
• we are needing a modern professional look

```html
<!DOCTYPE html>
<html lang="en">
<head>
<meta charset="utf-8">
<title>Lendquay</title>
<link href="https://fonts.googleapis.com/css2?family=Oswald:wght@300;400;500&family=Barlow:wght@400;500&family=Montserrat:wght@400;500&display=swap" rel="stylesheet">
<style>
:root{
  --orange:#e8431e;
  --ink:#222;
  --dark:#2b2b2b;
  --footer:#2d2d2d;
  --muted:#555;
  --line:#e3e3e3;
  --white:#fff;
}
*{box-sizing:border-box;margin:0;padding:0}
html,body{width:1200px;height:3151px;overflow:hidden;background:var(--white)}
body{position:relative;font-family:Arial,Helvetica,sans-serif;color:var(--ink)}
.brand{font-family:'Oswald',sans-serif;font-weight:400;letter-spacing:1px;line-height:1;white-space:nowrap}

/* header */
.site-header{position:absolute;left:0;top:0;width:1200px;height:126px;background:var(--white)}
.site-header .brand{position:absolute;left:110px;top:36px;font-size:44px;color:#111}
.main-nav{position:absolute;top:55px;font-family:'Oswald',sans-serif;font-size:14px;color:#222;letter-spacing:.3px}
.main-nav a{position:absolute;white-space:nowrap;text-decoration:none;color:inherit}
.main-nav a.active{color:var(--orange)}
.btn-login,.btn-signup{position:absolute;top:44px;height:40px;border-radius:3px;font-family:'Oswald',sans-serif;font-size:14px;color:#fff;display:flex;align-items:center;justify-content:center;letter-spacing:.4px}
.btn-login{left:850px;width:87px;background:var(--orange)}
.btn-signup{left:942px;width:145px;background:var(--dark)}

/* hero */
.hero{position:absolute;left:0;top:126px;width:1200px;height:755px;background:var(--orange);clip-path:polygon(0 0,100% 0,100% 644px,50% 755px,0 644px)}
.hero-photo{position:absolute;inset:0;background:radial-gradient(ellipse at 50% 40%,#6e5a48 0%,#3b312a 45%,#1a1714 100%);clip-path:polygon(0 0,100% 0,100% 640px,50% 718px,0 640px)}
.hero-shade{position:absolute;inset:0;background:rgba(0,0,0,.35)}
.hero-title{position:absolute;left:0;width:1200px;top:290px;text-align:center;font-family:'Oswald',sans-serif;font-weight:300;font-size:96px;line-height:1;color:#fff;letter-spacing:2px}
.hero-sub{position:absolute;left:0;width:1200px;top:414px;text-align:center;font-family:'Oswald',sans-serif;font-size:24px;line-height:36px;color:#fff}
.hero-cta{position:absolute;left:510px;top:505px;width:180px;height:53px;background:var(--orange);color:#fff;font-family:'Oswald',sans-serif;font-size:21px;display:flex;align-items:center;justify-content:center}
.hero-dots{position:absolute;top:700px;left:576px;display:flex;gap:6px}
.hero-dots span{width:12px;height:12px;border-radius:50%;background:#fff}
.hero-dots span.on{background:var(--orange)}

/* section heads */
.section-title{position:absolute;left:0;width:1200px;text-align:center;font-family:'Oswald',sans-serif;font-weight:400;font-size:46px;color:var(--dark);line-height:1}
.section-title em{font-style:normal;color:var(--orange)}
.section-sub{position:absolute;left:0;width:1200px;text-align:center;font-family:'Barlow',sans-serif;font-size:19px;color:#444}

/* feature cards */
.feature{position:absolute;width:471px;height:190px;border:2px solid var(--line);background:#fff;box-shadow:0 1px 4px rgba(0,0,0,.05)}
.feature svg{position:absolute;left:28px;top:48px}
.feature h3{position:absolute;left:150px;top:30px;font-family:'Oswald',sans-serif;font-weight:400;font-size:20px;color:#222}
.feature .rule{position:absolute;left:150px;top:67px;width:34px;height:2px;background:var(--orange)}
.feature p{position:absolute;left:153px;top:84px;width:300px;font-size:13.5px;line-height:27px;color:#666}

/* about */
.about{position:absolute;left:0;top:1588px;width:1200px;height:469px;background:var(--orange)}
.about-photo{position:absolute;left:0;top:0;width:585px;height:469px;background:linear-gradient(180deg,#c7d9ef 0%,#e6eef6 50%,#9b7a5a 70%,#6d4f36 100%)}
.about h2{position:absolute;left:638px;top:46px;font-family:'Oswald',sans-serif;font-weight:400;font-size:46px;line-height:1;color:#fff}
.about .rule{position:absolute;left:638px;top:105px;width:52px;height:2px;background:#fff}
.about p{position:absolute;left:638px;top:133px;width:437px;font-family:'Barlow',sans-serif;font-size:14px;line-height:27.5px;color:#fff;text-align:justify}
.about .read-more{position:absolute;left:640px;top:374px;width:139px;height:48px;background:var(--dark);color:#fff;font-family:'Oswald',sans-serif;font-size:18px;display:flex;align-items:center;justify-content:center;border-radius:2px}

/* rates honeycomb */
.rates{position:absolute;left:0;top:2245px;width:1200px;height:480px}
.rates text{font-family:'Oswald',sans-serif;font-size:14px;fill:#444;text-anchor:middle}

/* footer */
.site-footer{position:absolute;left:0;top:2795px;width:1200px;height:356px;background:var(--footer);color:#fff;font-family:'Montserrat',sans-serif}
.site-footer .brand{position:absolute;left:110px;top:86px;font-size:48px;color:#fff}
.social{position:absolute;left:120px;top:152px;display:flex;gap:7px}
.social span{width:36px;height:36px;border:2px solid #fff;border-radius:50%}
.footer-head{position:absolute;top:34px;font-family:'Oswald',sans-serif;font-size:17px;color:#fff}
.quick-links{position:absolute;left:405px;top:81px;list-style:none;font-size:13.5px}
.quick-links li{height:30px;display:flex;align-items:center;gap:14px}
.quick-links li::before{content:"\2192";font-size:15px}
.contact-row{position:absolute;left:594px;display:flex;align-items:flex-start;gap:16px;font-size:14px;line-height:24px}
.contact-row .ico{width:30px;height:30px;border-radius:50%;background:#3e3e3e;display:flex;align-items:center;justify-content:center;flex:none}
.news-text{position:absolute;left:870px;top:82px;width:230px;font-size:13px;line-height:21px}
.news-input{position:absolute;left:870px;top:139px;width:217px;height:39px;background:#fff;color:#666;font-size:12px;padding:12px 14px}
.news-submit{position:absolute;left:870px;top:191px;width:85px;height:32px;background:var(--orange);font-size:12px;font-weight:500;display:flex;align-items:center;justify-content:center}
.footer-bar{position:absolute;left:0;top:281px;width:1200px;height:75px;border-top:1px solid #3b3b3b;display:flex;align-items:center;justify-content:center;font-size:13px}
</style>
</head>
<body>

<header class="site-header">
  <div class="brand">LENDQUAY</div>
  <nav class="main-nav">
    <a class="active" style="left:417px">HOME</a>
    <a style="left:510px">ABOUT US</a>
    <a style="left:631px">SERVICES</a>
    <a style="left:751px">CONTACT US</a>
  </nav>
  <div class="btn-login">LOGIN</div>
  <div class="btn-signup">SIGN UP &nbsp;FOR FREE</div>
</header>

<section class="hero">
  <div class="hero-photo" role="img" aria-label="Smiling couple meeting with a broker at a table">
    <div class="hero-shade"></div>
    <div class="hero-title">LENDQUAY</div>
    <div class="hero-sub">SED UT PERSPICIATIS UNDE OMNIS ISTE NATUS ERROR SIT VOLUPTATEM<br>TOTAM REM ACCUSANTIUM DOLOREMQUE</div>
    <div class="hero-cta">GET STARTED</div>
    <div class="hero-dots"><span></span><span class="on"></span><span></span></div>
  </div>
</section>

<h2 class="section-title" style="top:936px">WHY <em>LENDQUAY?</em></h2>
<p class="section-sub" style="top:1003px">Sed ut perspiciatis unde omnis iste natus error sit voluptatem accusantium</p>

<div class="feature" style="left:111px;top:1102px">
  <svg width="86" height="86" viewBox="0 0 86 86" fill="none" stroke-width="3">
    <path d="M6 4v78h80" stroke="#222"/>
    <path d="M16 80V58h8v22M30 80V48h8v32M44 80V40h8v40M58 80V36h8v44M72 80V30h8v50" stroke="#222"/>
    <path d="M22 36l30-24" stroke="#e8431e"/><circle cx="22" cy="14" r="4" stroke="#e8431e"/><circle cx="46" cy="34" r="4" stroke="#e8431e"/>
  </svg>
  <h3>GREAT RATES &amp; INCENTIVES</h3><div class="rule"></div>
  <p>Nemo enim ipsam voluptatem quia voluptas sit asp ernatur aut odit aut fugit, sed quia &nbsp;onsequu ntur ma gni dolores eos qui ratione</p>
</div>
<div class="feature" style="left:616px;top:1102px">
  <svg width="96" height="96" viewBox="0 0 96 96" fill="none" stroke-width="3">
    <circle cx="58" cy="50" r="28" stroke="#e8431e"/><path d="M52 16h12M58 16v6M80 24l5-5" stroke="#e8431e"/>
    <path d="M58 50l-10 14" stroke="#e8431e"/>
    <path d="M4 40h30M10 50h22M4 60h28M14 70h18" stroke="#222"/>
  </svg>
  <h3>ANY TIME,ANY WHERE</h3><div class="rule"></div>
  <p>Nemo enim ipsam voluptatem quia voluptas sit asp ernatur aut odit aut fugit, sed quia &nbsp;onsequu ntur ma gni dolores eos qui ratione</p>
</div>
<div class="feature" style="left:111px;top:1330px">
  <svg width="86" height="96" viewBox="0 0 86 96" fill="none" stroke-width="3">
    <path d="M43 4L8 16v30c0 22 16 38 35 46 19-8 35-24 35-46V16z" stroke="#222"/>
    <rect x="26" y="44" width="34" height="28" rx="3" stroke="#e8431e"/><path d="M33 44v-8a10 10 0 0120 0v8" stroke="#e8431e"/><circle cx="43" cy="56" r="4" stroke="#e8431e"/><path d="M43 60v6" stroke="#e8431e"/>
  </svg>
  <h3>PRIVACY IS IMPORTANT</h3><div class="rule"></div>
  <p>Nemo enim ipsam voluptatem quia voluptas sit asp ernatur aut odit aut fugit, sed quia &nbsp;onsequu ntur ma gni dolores eos qui ratione</p>
</div>
<div class="feature" style="left:616px;top:1330px">
  <svg width="96" height="96" viewBox="0 0 96 96" fill="none" stroke-width="3">
    <circle cx="48" cy="22" r="18" stroke="#e8431e"/><path d="M54 14h-9a5 5 0 000 10h6a5 5 0 010 10h-9M48 10v32" stroke="#e8431e" stroke-width="2.5"/>
    <path d="M6 66c10-6 22-6 32 0h14a5 5 0 010 10H36M52 74l26-12a6 6 0 016 10L56 88H30L8 78" stroke="#222"/>
  </svg>
  <h3>NO FEES,NO OBLIGATIONS</h3><div class="rule"></div>
  <p>Nemo enim ipsam voluptatem quia voluptas sit asp ernatur aut odit aut fugit, sed quia &nbsp;onsequu ntur ma gni dolores eos qui ratione</p>
</div>

<section class="about">
  <div class="about-photo" role="img" aria-label="Model houses with a percent sign on a wooden table"></div>
  <h2>ABOUT US</h2><div class="rule"></div>
  <p>Sed ut perspiciatis unde omnis iste natus error sit voluptatem accusantium doloremque laudantium, totam rem aperiam, eaque ipsa quae ab illo inventore veritatis et quasi architecto beatae vitae dicta sunt explicabo. Nemo enim ipsam voluptatem quia voluptas sit aspernatur aut odit aut fugit, sed quia consequuntur magni dolores eos qui ratione voluptatem sequi nesciunt. Neque porro quisquam est, qui dolorem ipsum quia dolor sit amet, consectetur, adipisci velit, sed quia non quasi architecto beatae vitae numquam</p>
  <div class="read-more">READ MORE</div>
</section>

<h2 class="section-title" style="top:2120px">FIND &amp; <em>COMPARE RATES</em></h2>
<p class="section-sub" style="top:2187px">Sed ut perspiciatis unde omnis iste natus error sit voluptatem accusantium</p>

<svg class="rates" viewBox="0 1835 981 393" fill="none" stroke-width="2">
  <defs>
    <polygon id="hex" points="-78,0 -39,-67.5 39,-67.5 78,0 39,67.5 -39,67.5" stroke-width="9" fill="#fff"/>
  </defs>
  <g stroke="#6a2a8c"><use href="#hex" x="176" y="2137"/></g>
  <g stroke="#d9a49b"><use href="#hex" x="428" y="2137"/></g>
  <g stroke="#e8175d"><use href="#hex" x="679" y="2137"/></g>
  <g stroke="#c5d92d"><use href="#hex" x="302" y="2065"/></g>
  <g stroke="#5a3a4a"><use href="#hex" x="553" y="2065"/></g>
  <g stroke="#aaa3b8"><use href="#hex" x="804" y="2065"/></g>
  <g stroke="#e8431e"><use href="#hex" x="176" y="1992"/></g>
  <g stroke="#1e7fc8"><use href="#hex" x="428" y="1992"/></g>
  <g stroke="#2e3f94"><use href="#hex" x="679" y="1992"/></g>
  <g stroke="#f0b429"><use href="#hex" x="302" y="1920"/></g>
  <g stroke="#4ca53a"><use href="#hex" x="553" y="1920"/></g>
  <g stroke="#e01b24"><use href="#hex" x="804" y="1920"/></g>

  <g stroke="#e8431e"><path d="M160 1975v-12l16-12 16 12v12M170 1975v-8h12v8"/><circle cx="176" cy="1958" r="8"/></g>
  <g stroke="#f0b429"><circle cx="292" cy="1880" r="4"/><path d="M286 1888h12v14h-3v14h-6v-14h-3z"/><path d="M303 1914l8-8 5 4 10-10"/><circle cx="318" cy="1886" r="6"/></g>
  <g stroke="#1e7fc8"><rect x="416" y="1955" width="24" height="30"/><path d="M416 1962h24M416 1969h24M416 1976h24M424 1955v30M432 1955v30"/></g>
  <g stroke="#4ca53a"><path d="M533 1898l6-12h28l6 12v14h-40z"/><circle cx="541" cy="1907" r="3"/><circle cx="565" cy="1907" r="3"/></g>
  <g stroke="#2e3f94"><path d="M657 1955a22 12 0 0144 0"/><path d="M679 1943v-3"/><circle cx="672" cy="1962" r="4"/><circle cx="686" cy="1962" r="4"/><path d="M664 1975a8 8 0 0116 0M678 1975a8 8 0 0116 0"/></g>
  <g stroke="#e01b24"><circle cx="790" cy="1880" r="4"/><circle cx="818" cy="1880" r="4"/><circle cx="804" cy="1876" r="4"/><path d="M784 1892h40M790 1892v16M818 1892v16M798 1888h12"/></g>
  <g stroke="#c5d92d"><path d="M278 2042l5-10h26l5 10v12h-36z"/><circle cx="286" cy="2048" r="3"/><circle cx="306" cy="2048" r="3"/><path d="M312 2022l8-4 8 4v8c0 5-4 8-8 10-4-2-8-5-8-10z"/></g>
  <g stroke="#5a3a4a"><path d="M553 2048v-22M553 2030c-8 0-12-6-12-12 8 0 12 6 12 12zM553 2030c8 0 12-6 12-12-8 0-12 6-12 12zM537 2054c5-6 27-6 32 0"/></g>
  <g stroke="#aaa3b8"><path d="M810 2028l-16 22h12l-6 20 18-26h-12z"/></g>
  <g stroke="#6a2a8c"><path d="M158 2128l5-10h26l5 10v12h-36z"/><circle cx="166" cy="2134" r="3"/><circle cx="186" cy="2134" r="3"/><path d="M196 2112l12-12 6 6-12 12"/></g>
  <g stroke="#d9a49b"><circle cx="428" cy="2120" r="18"/><ellipse cx="428" cy="2120" rx="8" ry="18"/><path d="M410 2120h36M413 2110h30M413 2130h30"/></g>
  <g stroke="#e8175d"><rect x="667" y="2104" width="22" height="36" rx="3"/><path d="M667 2132h22M675 2108h6"/></g>

  <text x="176" y="2019">MORTGAGE</text><text x="176" y="2040">RATES</text>
  <text x="302" y="1947">PERSONAL</text><text x="302" y="1968">FINANCE</text>
  <text x="428" y="2019">COMMERCIAL</text><text x="428" y="2040">FINANACE</text>
  <text x="553" y="1947">VECHICLE</text><text x="553" y="1968">FINANACE</text>
  <text x="679" y="2023">INSURANCE</text><text x="679" y="2044">RATES</text>
  <text x="804" y="1947">BUSINESS &amp;</text><text x="804" y="1968">ASSET FINANCE</text>
  <text x="302" y="2088">HOME,CONTENTS &amp;</text><text x="302" y="2109">CAR INSURANCE</text>
  <text x="553" y="2086">FARMING &amp;</text><text x="553" y="2107">RURAL INSURANCE</text>
  <text x="804" y="2100">POWER &amp; GAS</text>
  <text x="176" y="2166">VEHICLE</text><text x="176" y="2187">LEASING</text>
  <text x="428" y="2170">INTERNET &amp; FIBER</text>
  <text x="679" y="2177">PHONE &amp; MOBILE</text>
</svg>

<footer class="site-footer">
  <div class="brand">LENDQUAY</div>
  <div class="social"><span></span><span></span><span></span><span></span><span></span></div>

  <div class="footer-head" style="left:405px">QUICK LINKS</div>
  <ul class="quick-links">
    <li>HOME</li><li>ABOUT US</li><li>CAREERS</li><li>MEDIA</li><li>SUPPORT</li><li>CONTACT US</li>
  </ul>

  <div class="footer-head" style="left:594px">CONTACT US</div>
  <div class="contact-row" style="top:80px"><span class="ico"><svg width="12" height="12" viewBox="0 0 12 12"><path d="M2 1l2 0 1 3-1.5 1a7 7 0 003.5 3.5L8 7l3 1v2a1 1 0 01-1 1A9 9 0 011 2a1 1 0 011-1z" fill="#fff"/></svg></span><span style="padding-top:3px">0508 41 63 90</span></div>
  <div class="contact-row" style="top:129px"><span class="ico"><svg width="13" height="10" viewBox="0 0 13 10" fill="none" stroke="#fff"><rect x=".5" y=".5" width="12" height="9"/><path d="M.5 .5l6 5 6-5"/></svg></span><span style="padding-top:3px">info@lendquay.co.nz</span></div>
  <div class="contact-row" style="top:176px"><span class="ico"><svg width="10" height="13" viewBox="0 0 10 13"><path d="M5 0a5 5 0 015 5c0 4-5 8-5 8S0 9 0 5a5 5 0 015-5z" fill="#fff"/><circle cx="5" cy="5" r="2" fill="#3e3e3e"/></svg></span><span style="padding-top:3px">14 Harbour Lane, Auckland 1010,<br>New Zealand</span></div>

  <div class="footer-head" style="left:870px">NEWSLETTER</div>
  <p class="news-text">Sed ut perspiciatis unde omni us error sit voluptatem</p>
  <div class="news-input">Email :</div>
  <div class="news-submit">SUBMIT</div>

  <div class="footer-bar">© Copyrights 2020 - Lendquay.All Rights Reserved.</div>
</footer>

</body>
</html>
```